RESIDENTIAL CONSTRUCTION

We are a company that specializes in building custom residential homes, the design should also emphasize that quality and service is our priority.

Industry/Entity Type

Construction Company

Contact Information for Business Card

Contact Person: Marcus Lindqvist
Company Address: 273 West Alder Ave San Jose , Ca 95380
Phone Number : 408-731-2946
Email Address: Stoneridgehomes517@mailvista.net

Font styles to use
Sans Serif

Colors
ec1f27

Requirements
Must have
• CSLB # 7362015
Nice to have
• needs to have same color as logo i uploaded, we will be printing these on a clear plastic card.

```html
<!DOCTYPE html>
<html lang="en">
<head>
<meta charset="utf-8">
<title>Stoneridge Homes – Business Card</title>
<link rel="stylesheet" href="https://fonts.googleapis.com/css2?family=Open+Sans:wght@400;700&display=swap">
<style>
  :root {
    --brand-red: #ec1f27;
    --deep-red: #c8202f;
    --ink: #111111;
    --card-black: #0b0b0b;
    --paper: #ffffff;
    --steel: #b9b9bd;
    --stage: #2a2a2a;
  }
  * { box-sizing: border-box; margin: 0; padding: 0; }
  html, body { width: 1200px; height: 1200px; overflow: hidden; }
  body {
    background: var(--stage);
    font-family: "Open Sans", Arial, sans-serif;
    position: relative;
  }
  .card {
    position: absolute;
    left: 150px;
    width: 900px;
    height: 514px;
    overflow: hidden;
  }
  .card--back { top: 70px; background: var(--card-black); }
  .card--front { top: 616px; background: var(--paper); color: var(--ink); }

  .ruler-band { position: absolute; left: 0; width: 100%; }
  .card--back .ruler-band { height: 60px; background: linear-gradient(#2a2a2a, #505050); opacity: .75; }
  .card--back .ruler-band--top { top: 0; }
  .card--back .ruler-band--bottom { bottom: 0; background: linear-gradient(#505050, #2a2a2a); }

  .brand {
    position: absolute;
    display: flex; align-items: center; gap: 16px;
    font-weight: 700;
    text-transform: uppercase;
    letter-spacing: 2px;
    line-height: 1;
    white-space: nowrap;
  }
  .brand__mark { width: 34px; height: 34px; flex: none; }
  .card--back .brand { left: 50%; top: 50%; transform: translate(-50%, -50%); color: var(--steel); font-size: 58px; }
  .card--back .brand__mark { background: var(--steel); }
  .card--front .brand { left: 140px; top: 92px; color: var(--brand-red); font-size: 54px; }
  .card--front .brand__mark { background: var(--brand-red); }

  .name-bar {
    position: absolute; left: 260px; top: 250px;
    width: 360px; height: 58px;
    background: var(--ink); color: var(--paper);
    font-weight: 700; font-size: 27px; letter-spacing: .5px;
    display: flex; align-items: center; justify-content: center;
    text-transform: uppercase; white-space: nowrap;
  }
  .rule { position: absolute; height: 2px; background: var(--ink); }
  .rule--upper { left: 620px; top: 250px; width: 240px; }
  .rule--lower { left: 40px; top: 306px; width: 220px; }

  .address {
    position: absolute; right: 40px; top: 262px;
    text-align: right; font-size: 23px; line-height: 1.35; white-space: nowrap;
  }
  .contact {
    position: absolute; left: 42px; top: 320px;
    font-size: 23px; line-height: 1.35; white-space: nowrap;
  }
  .card--front .ruler-band {
    bottom: 16px; height: 56px;
    background: linear-gradient(var(--paper), #cfcfcf);
  }
  .accent-strip {
    position: absolute; left: 0; bottom: 0; width: 100%; height: 16px;
    background: var(--deep-red);
  }
</style>
</head>
<body>
  <section class="card card--back" aria-label="Card back">
    <div class="ruler-band ruler-band--top" role="img" aria-label="Ruler tick marks along the top edge"></div>
    <div class="brand"><span class="brand__mark"></span>Stoneridge Homes</div>
    <div class="ruler-band ruler-band--bottom" role="img" aria-label="Ruler tick marks along the bottom edge"></div>
  </section>

  <section class="card card--front" aria-label="Card front">
    <div class="brand"><span class="brand__mark"></span>Stoneridge Homes</div>
    <div class="rule rule--upper"></div>
    <div class="name-bar">Marcus Lindqvist</div>
    <div class="address">273 West Alder Ave<br>San Jose , Ca 95380</div>
    <div class="rule rule--lower"></div>
    <div class="contact">P: 408-731-2946<br>Stoneridgehomes517@mailvista.net<br>CSLB # 7362015</div>
    <div class="ruler-band" role="img" aria-label="Ruler tick marks along the bottom edge"></div>
    <div class="accent-strip"></div>
  </section>
</body>
</html>
```